Health Care Company with Logo Needs Business Cards designed

We are a luxury behavioral health company looking for business cards design we already have a logo and are looking for someone to design a sophisticated luxurious looking business card. Please note that Card design should be captivating just like the logo and also encompass the logo color

Industry/Entity Type

Healthcare

Contact Information for Business Card

Logo,company name, tagline, my name and title, contact details, and physical address

```html
<!DOCTYPE html>
<html lang="en">
<head>
<meta charset="utf-8">
<title>Marlow Behavioral Health – Business Cards</title>
<link rel="stylesheet" href="https://fonts.googleapis.com/css2?family=Roboto+Condensed:wght@700&family=Open+Sans:wght@400;600&family=Roboto:wght@500&display=swap">
<style>
  :root {
    --backdrop: #2b2b2b;
    --card: #f1f1f1;
    --purple: #6b2f86;
    --blue: #1b8ac9;
    --orange: #e08a1e;
    --green: #7eab2d;
    --ink: #2a2a2a;
  }
  * { margin: 0; padding: 0; box-sizing: border-box; }
  html, body {
    width: 1200px; height: 1138px; overflow: hidden;
    background: var(--backdrop);
  }
  .canvas { position: relative; width: 1200px; height: 1138px; }
  .card {
    position: absolute;
    background: var(--card);
    border-radius: 16px;
    overflow: hidden;
  }
  .card--front { left: 274px; top: 186px; width: 623px; height: 376px; }
  .card--back  { left: 276px; top: 608px; width: 618px; height: 374px; }

  .brand-name {
    font-family: "Roboto Condensed", "Arial Narrow", sans-serif;
    font-weight: 700;
    color: var(--purple);
    white-space: nowrap;
    line-height: 1;
  }
  .tagline {
    font-family: "Roboto Condensed", "Arial Narrow", sans-serif;
    font-weight: 700;
    color: var(--blue);
    text-transform: uppercase;
    white-space: nowrap;
    line-height: 1;
  }

  .front-lockup {
    position: absolute; left: 0; right: 0; top: 156px;
    text-align: center;
  }
  .front-lockup .brand-name { font-size: 43px; }
  .front-lockup .tagline { font-size: 13px; letter-spacing: 3.7px; margin-top: 8px; }

  .brand-mark {
    position: absolute; left: 36px; top: 55px;
    width: 58px; height: 58px;
    background: var(--purple);
  }
  .back-lockup { position: absolute; left: 129px; top: 62px; }
  .back-lockup .brand-name { font-size: 37px; }
  .back-lockup .tagline { font-size: 11.5px; letter-spacing: 3.3px; margin-top: 7px; }

  .person-name {
    position: absolute; left: 36px; top: 252px;
    font-family: "Roboto", Arial, sans-serif;
    font-weight: 500;
    font-size: 22px;
    color: var(--purple);
    text-transform: uppercase;
  }
  .contact {
    position: absolute; left: 36px; top: 292px;
    font-family: "Open Sans", Arial, sans-serif;
    font-size: 14px;
    line-height: 22px;
    color: var(--ink);
    white-space: nowrap;
  }
  .contact .label { color: var(--purple); }
  .contact .sep { color: var(--purple); margin: 0 7px; }

  .color-band {
    position: absolute; left: 0; right: 0; bottom: 0;
    height: 8px; display: flex;
  }
  .color-band span { flex: 1; }
  .color-band .orange { background: var(--orange); }
  .color-band .blue { background: var(--blue); }
  .color-band .green { background: var(--green); }
  .color-band .purple { background: var(--purple); }
</style>
</head>
<body>
<main class="canvas">
  <section class="card card--front" aria-label="Card front">
    <div class="front-lockup">
      <div class="brand-name">Marlow Behavioral Health</div>
      <div class="tagline">Devoted to peace, wellness and renewal</div>
    </div>
  </section>

  <section class="card card--back" aria-label="Card back">
    <div class="brand-mark" aria-hidden="true"></div>
    <div class="back-lockup">
      <div class="brand-name">Marlow Behavioral Health</div>
      <div class="tagline">Devoted to peace, wellness and renewal</div>
    </div>

    <div class="person-name">Daniel Reeve</div>
    <div class="contact">
      <div>
        <span class="label">P:</span> 555-210-4830<span class="sep">|</span><span class="label">E:</span> dan@marlowhealth.com<span class="sep">|</span><span class="label">W:</span> www.marlowhealth.com
      </div>
      <div><span class="label">A:</span> 48 Linden Ave, Suite 2, Brookfield, US 10234</div>
    </div>

    <div class="color-band" aria-hidden="true">
      <span class="orange"></span><span class="blue"></span><span class="green"></span><span class="purple"></span>
    </div>
  </section>
</main>
</body>
</html>
```